Business Card Design

New business card design

Target Market(s)

Residential & Commercial Property Managers

Industry/Entity Type

Plumbing Services

Contact Information for Business Card

Name - Rowan Keddle, title - Director, Phone Number - 0431 286 517, email - rowan@tbk-plumbing.com.au, Company ABN - 73 215 904 386,

Font styles to use
Sans Serif

Colors
0054AA
0677BA
7BADD7
CADEEF
E8F1F8

```html
<!DOCTYPE html>
<html lang="en">
<head>
<meta charset="utf-8">
<title>TBK Plumbing Services – Business Card</title>
<link href="https://fonts.googleapis.com/css2?family=Montserrat:wght@400;500;700&display=swap" rel="stylesheet">
<style>
  :root {
    --ink: #1e2832;
    --aqua: #2aa7e0;
    --paper: #ffffff;
    --backdrop: #e6e8ea;
  }
  * { margin: 0; padding: 0; box-sizing: border-box; }
  html, body {
    width: 1200px; height: 900px; overflow: hidden;
    background: var(--backdrop);
    font-family: "Montserrat", Arial, sans-serif;
    color: var(--ink);
  }
  .sheet {
    width: 1200px; height: 900px;
    display: flex; flex-direction: column;
    align-items: center; justify-content: center; gap: 48px;
  }
  .card {
    position: relative;
    width: 640px; height: 366px;
    background: var(--paper);
    border-radius: 22px;
    overflow: hidden;
    box-shadow: 0 10px 28px rgba(30, 40, 50, 0.18);
  }
  .brand {
    display: flex; align-items: center; gap: 14px;
    font-weight: 500; color: var(--ink);
    letter-spacing: 0.02em; white-space: nowrap;
  }
  .brand__dot {
    width: 22px; height: 22px; border-radius: 50%;
    background: var(--aqua); flex: none;
  }
  .card--front { display: flex; align-items: center; justify-content: center; }
  .card--front .brand { font-size: 40px; }

  .card--back .brand {
    position: absolute; top: 44px; left: 0; right: 0;
    justify-content: center; font-size: 34px;
  }
  .card__swoosh { position: absolute; inset: 0; }
  .holder {
    position: absolute; left: 50px; top: 146px;
    display: flex; align-items: center;
  }
  .holder__id { text-align: right; padding-right: 20px; }
  .holder__name { font-weight: 700; font-size: 30px; color: var(--aqua); line-height: 1.1; white-space: nowrap; }
  .holder__role { font-size: 19px; margin-top: 4px; }
  .holder__rule { width: 1.5px; height: 88px; background: var(--aqua); flex: none; }
  .contact { list-style: none; padding-left: 20px; font-size: 16px; }
  .contact li { display: flex; align-items: center; gap: 10px; line-height: 1.8; white-space: nowrap; }
  .contact svg { width: 16px; height: 16px; flex: none; }
  .abn {
    position: absolute; left: 50px; top: 258px;
    font-size: 16px; color: var(--ink); white-space: nowrap;
  }
</style>
</head>
<body>
<main class="sheet">
  <section class="card card--front">
    <div class="brand"><span class="brand__dot"></span>tbk plumbing services</div>
  </section>

  <section class="card card--back">
    <svg class="card__swoosh" viewBox="0 0 640 366" preserveAspectRatio="none" aria-hidden="true">
      <path d="M0,364 Q390,352 640,266 L640,366 L0,366 Z" fill="var(--ink)"/>
      <path d="M50,352 Q400,336 640,250" fill="none" stroke="var(--aqua)" stroke-width="3"/>
    </svg>

    <div class="brand"><span class="brand__dot"></span>tbk plumbing services</div>

    <div class="holder">
      <div class="holder__id">
        <p class="holder__name">Rowan Keddle</p>
        <p class="holder__role">Director</p>
      </div>
      <div class="holder__rule"></div>
      <ul class="contact">
        <li>
          <svg viewBox="0 0 24 24" aria-hidden="true"><path fill="var(--aqua)" d="M6.6 10.8a15.1 15.1 0 0 0 6.6 6.6l2.2-2.2a1 1 0 0 1 1-.25 11.4 11.4 0 0 0 3.6.57 1 1 0 0 1 1 1V20a1 1 0 0 1-1 1A17 17 0 0 1 3 4a1 1 0 0 1 1-1h3.5a1 1 0 0 1 1 1c0 1.25.2 2.45.57 3.57a1 1 0 0 1-.25 1z"/></svg>
          0431 286 517
        </li>
        <li>
          <svg viewBox="0 0 24 24" aria-hidden="true"><rect x="2" y="5" width="20" height="14" rx="2" fill="var(--aqua)"/><path d="M3 6l9 7 9-7" fill="none" stroke="#fff" stroke-width="1.8"/></svg>
          rowan@tbk-plumbing.com.au
        </li>
      </ul>
    </div>

    <p class="abn">Company ABN - 73 215 904 386</p>
  </section>
</main>
</body>
</html>
```